July 2022 Industrial Manufacturer Product Expo Mexico City

We manufacture large screws and fastners for large Mining equipment, Trains, large ships, airplanes, wind turbines, and so on. We also do custom work base on the customer needs. No matter the size we can make it.
We have a Expo coming up with companies all over the world. We have to stand out we are a family own business so our customer service will be above and beyond anyone can provide. We do not have a sales force to push our products and services we provide one on one service.
Plus@!! I'm looking for anything that you designers can come up with if it was your company to put on a business card, plus i want to do a 1 or 2 sided pamphlet, and then a website. We make Speciality Bolts for large mining equipment these bolts can be 3 to 4 foot long!!! Plus fasteners, Nuts, washers, any, size, strengths, special materials, we offer more of a ono on one customer service, We are a small company, family own, but can fulfill any type of orders. We can also provide special time lines for emergency orders. "We keep the machines running we here at KRV don't believe in down time" We want to hear any slogan based on our company to stand out.
Thanks i really appreciate all your work and options that we have to pick on. Plus just a thought we could possibly want to entertain a experience Marketing internet help maybe a employment possibility. Thanks

I need 2 cards one in Spanish and English Like the steel back ground maybe send me in some bright red and blue writing Same with the Black cards Please remove the word Military The logo KRV maybe integrate a picture of a Bolt 🔩 Thank you

Still looking for I need 2 cards one in Spanish and English Like the steel back ground maybe send me in some bright red and blue writing Same with the Black cards try bright writing Please remove the word Military The logo KRV maybe integrate a picture of a Bolt 🔩 Plus will need the company to make a brochure and website next Thank you

Target Market(s)

Large Mining, Ship, Train, Green Energy, VELM, and Government equipment. Throughout the World

Industry/Entity Type

We can Custom Manufacture any type of Fastners for Mining equipment, Trains, Ships, Green energy, Governments, or military projects. wind turbines,

Contact Information for Business Card

I attached the name and contact info that's on a card, plus the Company Logo. Would like industrial looking background with Bright Colors that will stand out!! If we can insert somewhere maybe on back that we "Custom Manufacture Any Size or Quantity Fastners for Large Mining Equipment, Trains, Ships, Green Energy Equipment or Government Projects

Font styles to use
Other font styles liked:
• You Pick, has to be bold, colorful standout, Professional looking Beable to read it.

Colors

Designer to choose colors to be used in the design.

Requirements
Must have
• Need in Spanish and English TO STANDOUT FROM THE REST OF THE EXPO!! See Business card details, Rounded corners
Nice to have
• Can i see some of the darker cards with Bright Red and Blue letters I like to see the different type of card material, heavy thickness, plastic, transparent, Metal types, Bright Colors, I saw like Raised letters like on the logo.

```html
<!DOCTYPE html>
<html lang="es">
<head>
<meta charset="utf-8">
<title>KRV – Tarjetas de presentación</title>
<link rel="stylesheet" href="https://fonts.googleapis.com/css2?family=Source+Sans+3:wght@400;600&family=Tinos&display=swap">
<style>
  :root {
    --backdrop: #b5b5b5;
    --navy: #001a78;
    --sky: #0095d6;
    --white: #ffffff;
    --graphite: #55595f;
    --band-top: #0a3596;
    --band-bottom: #0389d2;
    --shadow: rgba(0, 0, 0, 0.55);
    --corner: 14px;
  }
  * { box-sizing: border-box; margin: 0; padding: 0; }
  html, body {
    width: 1075px;
    height: 1200px;
    overflow: hidden;
    background: var(--backdrop);
  }
  .sheet {
    position: relative;
    width: 1075px;
    height: 1200px;
  }
  .card {
    position: absolute;
    left: 206px;
    width: 663px;
    border-radius: var(--corner);
    box-shadow: 3px 3px 3px var(--shadow);
    overflow: hidden;
  }
  /* Front */
  .card--front {
    top: 187px;
    height: 395px;
    background: var(--navy);
    font-family: "Source Sans 3", sans-serif;
    color: var(--white);
  }
  .front__accent {
    position: absolute;
    left: 0;
    top: 0;
    width: 390px;
    height: 395px;
    background: linear-gradient(160deg, var(--navy) 0%, #1a3f9e 45%, var(--sky) 100%);
  }
  .front__details {
    position: absolute;
    right: 38px;
    top: 59px;
    text-align: right;
  }
  .front__name {
    font-size: 24px;
    font-weight: 600;
    color: var(--sky);
  }
  .front__quote {
    margin-top: 12px;
    font-size: 19px;
    line-height: 23px;
    letter-spacing: 0.2px;
  }
  .front__phones {
    position: absolute;
    right: 41px;
    top: 298px;
    list-style: none;
    font-size: 18px;
    line-height: 24px;
    letter-spacing: 0.3px;
  }
  .front__phones li {
    display: flex;
    align-items: center;
    justify-content: flex-end;
    gap: 9px;
  }
  .front__phones svg { width: 16px; height: 16px; }

  /* Back */
  .card--back {
    top: 637px;
    height: 396px;
    background: var(--white);
  }
  .back__brand {
    position: absolute;
    left: 0;
    right: 0;
    top: 100px;
    text-align: center;
    font-family: "Source Sans 3", sans-serif;
    font-weight: 600;
    font-size: 96px;
    letter-spacing: 6px;
    color: var(--graphite);
  }
  .back__band {
    position: absolute;
    left: 0;
    bottom: 0;
    width: 100%;
    height: 106px;
    background: linear-gradient(180deg, var(--band-top) 0%, var(--band-bottom) 100%);
    display: flex;
    align-items: center;
    justify-content: center;
  }
  .back__tagline {
    font-family: "Tinos", serif;
    color: var(--white);
    font-size: 19px;
    line-height: 23px;
    text-align: center;
    width: 500px;
  }
</style>
</head>
<body>
<main class="sheet">
  <section class="card card--front" aria-label="Frente de la tarjeta">
    <div class="front__accent" role="img" aria-label="Brand mark area in blue tones"></div>
    <div class="front__details">
      <p class="front__name">Lic. Mariela Soto Ibarra</p>
      <p class="front__quote">Cotizaciones en<br>ventas@krvtornilleria.mx</p>
    </div>
    <ul class="front__phones">
      <li>8712046318
        <svg viewBox="0 0 16 16" aria-hidden="true">
          <path d="M3.2 1.5l2.3 2.4-1.3 1.7c.9 2 2.5 3.6 4.4 4.5l1.7-1.3 2.4 2.3-1.6 2.4C6.6 13.2 2.6 9.2 1.3 4.5z" fill="none" stroke="#fff" stroke-width="1.6" stroke-linejoin="round"/>
          <path d="M9.5 1.8a5 5 0 0 1 4.7 4.7M9.4 4.3a2.4 2.4 0 0 1 2.3 2.3" fill="none" stroke="#fff" stroke-width="1.4" stroke-linecap="round"/>
        </svg>
      </li>
      <li>8719350274
        <svg viewBox="0 0 16 16" aria-hidden="true">
          <rect x="3.5" y="1" width="9" height="14" rx="1.5" fill="none" stroke="#fff" stroke-width="1.6"/>
          <line x1="6.5" y1="12.5" x2="9.5" y2="12.5" stroke="#fff" stroke-width="1.4"/>
        </svg>
      </li>
    </ul>
  </section>

  <section class="card card--back" aria-label="Reverso de la tarjeta">
    <p class="back__brand">KRV</p>
    <div class="back__band">
      <p class="back__tagline">Custom Manufacture Any Size or Quantity Fastners for Large Mining Equipment, Trains, Ships, Green Energy Equipment or Government Projects</p>
    </div>
  </section>
</main>
</body>
</html>
```